LB - WESITE NEEDED PAGE: Clean / Modern / Pro & Dynamic

Lantern-Brokers is a new insurance brokerage firm dealing exclusively with companies (BToB) providing the following property: Liabilities Insurance Insurances Automobile Insurance Insurances Construction% 26amp; Engineering Casualty Workmen 's Compensation Health Insurance Marime% 26amp; Transit Credit Insurance Young, Fast, Proactive and Dynamic we call ourselves Lantern-Brokers because we are a "start-up" willing to make a difference in the market, bringing modernity and speed to our industry, still too bureaucratic / procedural / opaque uninitiated. We need something respecting the colors of our orange logtype; blue; white; black; easy to scroll, with simple information on the company; - who we are - our team (with the pictures) - what we do - what we do - contact us, contact us (google map) Luanda (Angola) Small company, just need something flashy / professional / structured / modern.

Target Market(s)

BtoB; Oil and gas companies; French speaking copying established in Angola, all industrials, factories and importers of goods.

Industry/Entity Type

Insurance Broker

Font styles to use
Sans Serif

Colors

Designer to choose colors to be used in the design.

Requirements
Must have
• We need something respecting the colors of our orange logtype; blue; white; black; easy to scroll, with simple information on the company; - who we are - our team (with the pictures) - what we do - what we do - contact us, contact us (google map) Luanda (Angola) Small company, just need something flashy / professional / structured / modern.
Nice to have
• A page format
Should not have
• WE DO NOT WANT A REFER TO OUR LOGO, but a Home Page for our Website with the basics categories ... >> PLEASE CAREFULLY USE THE RIGHT COLOR OF THE LOGOTYPE which are the ones enclosed Orange / Turquoise / Black as per the business card .

```html
<!DOCTYPE html>
<html lang="en">
<head>
<meta charset="utf-8">
<title>Lantern-Brokers | Insurance Brokers</title>
<link rel="stylesheet" href="https://fonts.googleapis.com/css2?family=Exo+2:wght@600;700&family=Montserrat:wght@400;500;600&display=swap">
<style>
:root{
  --orange:#f2612a;
  --orange-light:#ff8a3d;
  --blue:#1b8fe6;
  --ink:#1d1d1d;
  --muted:#9a9a9a;
  --grey-band:#f5f5f5;
  --line:#e3e3e3;
  --footer:#0b0b0b;
  --header:#39434f;
  --white:#ffffff;
}
*{margin:0;padding:0;box-sizing:border-box}
html,body{width:1200px;height:3617px;overflow:hidden}
body{position:relative;font-family:"Montserrat",sans-serif;color:var(--ink);background:var(--white)}
.abs{position:absolute}
.display{font-family:"Exo 2",sans-serif;font-weight:700}

/* header */
.site-header{position:absolute;left:0;top:0;width:1200px;height:70px;background:rgba(45,55,66,.92);z-index:3}
.brand{position:absolute;left:147px;top:22px;display:flex;align-items:center;gap:8px;font-weight:600;font-size:15px;color:var(--orange)}
.brand-dot{width:20px;height:20px;border-radius:50%;background:var(--orange)}
.nav{position:absolute;top:29px;font-size:11px;font-weight:500;color:#fff;letter-spacing:.4px}
.nav.active{color:var(--orange)}
.phone{position:absolute;left:936px;top:22px;display:flex;align-items:center;gap:9px;color:#fff;font-size:12px}
.phone-ring{width:27px;height:27px;border-radius:50%;border:2px solid var(--orange);display:flex;align-items:center;justify-content:center}

/* hero */
.hero{position:absolute;left:0;top:0;width:1200px;height:618px;background:linear-gradient(100deg,#f2f3f4 0%,#e4e6e8 45%,#c8cdd3 75%,#9aa3ad 100%)}
.hero-photo{position:absolute;left:190px;top:70px;width:1010px;height:548px;background:linear-gradient(180deg,rgba(255,255,255,0) 40%,rgba(140,80,50,.45) 78%,rgba(230,225,220,.8) 100%)}
.hero-title{position:absolute;left:140px;top:255px;font-size:38px;line-height:43px;color:#151515;letter-spacing:.5px}
.hero-sub{position:absolute;left:141px;top:345px;font-size:12.5px;line-height:17px;font-weight:500;color:#222;width:400px}
.btn{position:absolute;height:31px;border-radius:16px;background:linear-gradient(90deg,var(--orange),var(--orange-light));color:#fff;font-size:11.5px;font-weight:500;display:flex;align-items:center;justify-content:center;letter-spacing:.3px}
.btn-dot{position:absolute;width:22px;height:22px;border-radius:50%;background:var(--blue)}
.mouse{position:absolute;left:575px;top:590px;width:50px;height:40px;border-radius:25px 25px 0 0;background:#fff}

/* section heads */
.kicker{position:absolute;left:0;width:1200px;text-align:center;font-size:12.5px;color:var(--blue)}
.sec-title{position:absolute;left:0;width:1200px;text-align:center;font-size:34px;color:#111}
.sec-rule{position:absolute;left:573px;width:54px;height:2px;background:var(--blue)}
.sec-lead{position:absolute;left:0;width:1200px;text-align:center;font-size:10px;color:var(--muted)}

/* about */
.about-photo{position:absolute;left:159px;top:807px;width:437px;height:296px;background:#fff;box-shadow:0 2px 12px rgba(0,0,0,.18);padding:8px}
.about-photo div{width:100%;height:100%;background:linear-gradient(135deg,#c9d3dc,#8f9eae 55%,#4d5a66)}
.about-heading{position:absolute;left:636px;top:810px;font-size:17px;line-height:23px;font-weight:500;color:var(--orange)}
.about-text{position:absolute;left:636px;top:862px;width:418px;font-size:10px;line-height:19px;color:var(--muted);text-align:justify}
.about-stem{position:absolute;left:715px;top:1026px;width:1px;height:38px;background:#ccc}

/* services */
.services{position:absolute;left:0;top:1173px;width:1200px;height:455px;background:var(--grey-band)}
.service{position:absolute;top:1358px;width:190px;text-align:center}
.service svg{display:block;margin:0 auto}
.service-label{margin-top:18px;font-size:12.5px;line-height:17px;font-weight:500;color:#111}
.service.featured .service-label{color:var(--orange)}

/* testimonial */
.testimonial{position:absolute;left:0;top:1628px;width:1200px;height:442px;background:linear-gradient(120deg,#4a5563,#6b7480 45%,#8e8478 70%,#5c5f66)}
.testimonial::after{content:"";position:absolute;inset:0;background:rgba(40,48,60,.45)}
.t-layer{position:absolute;left:0;top:0;width:1200px;height:442px;z-index:1;color:#fff}
.avatar{position:absolute;left:563px;top:169px;width:72px;height:72px;border-radius:50%;background:linear-gradient(160deg,#d5dbe2,#6a7b8e);border:3px solid #fff}
.t-name{position:absolute;left:655px;top:188px;font-size:12px;font-weight:500}
.t-role{position:absolute;left:655px;top:207px;font-size:9px;font-style:italic;color:#dcdcdc}
.t-quote{position:absolute;left:270px;top:256px;width:660px;text-align:center;font-size:11px;line-height:18px}
.dots{position:absolute;left:582px;top:365px;display:flex;gap:8px}
.dots span{width:6px;height:6px;border-radius:50%;background:#fff}
.dots span.on{background:var(--orange)}

/* team */
.member{position:absolute;top:2243px;width:213px;height:311px;background:#fff;box-shadow:0 1px 6px rgba(0,0,0,.12);text-align:center}
.member-photo{width:213px;height:181px;background:linear-gradient(180deg,#e6e8ea 0%,#b9c0c8 55%,#2c3e62 100%)}
.member-name{margin-top:24px;font-size:12.5px;color:#222}
.member-role{margin-top:4px;font-size:11px;font-style:italic;color:var(--orange)}
.member-bio{margin:8px auto 0;width:180px;font-size:9.5px;line-height:16px;color:var(--muted)}
.member-social{position:absolute;left:0;top:45px;width:22px;height:82px;background:#fff;display:flex;flex-direction:column;align-items:center;justify-content:space-around;padding:6px 0}
.member-social span{width:8px;height:8px;background:#222}

/* contact */
.contact{position:absolute;left:0;top:2619px;width:1200px;height:575px;background:#fafafa}
.field{position:absolute;height:42px;background:#fff;border:1px solid var(--line);border-radius:3px;font-size:10px;color:#444;padding:14px 11px}
.field.message{height:94px}

/* newsletter */
.newsletter{position:absolute;left:0;top:3194px;width:1200px;height:72px;background:linear-gradient(90deg,#f25a22,#ff8f3f 60%,#ff9a45)}
.nl-icon{position:absolute;left:151px;top:19px;width:34px;height:34px;border-radius:50%;border:2px solid #fff;background:var(--blue);display:flex;align-items:center;justify-content:center}
.nl-title{position:absolute;left:198px;top:20px;font-size:24px;color:#fff}
.nl-input{position:absolute;left:484px;top:21px;width:352px;height:31px;background:#fff;font-size:10px;color:#444;padding:10px 10px}
.nl-btn{position:absolute;left:862px;top:21px;width:119px;height:31px;border-radius:16px;background:var(--blue);color:#fff;font-size:12.5px;display:flex;align-items:center;justify-content:center}

/* footer */
.footer{position:absolute;left:0;top:3266px;width:1200px;height:316px;background:var(--footer);color:#fff}
.f-head{position:absolute;top:40px;font-size:21px;letter-spacing:.5px}
.f-rule{position:absolute;top:74px;height:2px;width:122px;background:var(--blue)}
.f-link{position:absolute;left:145px;font-size:11px;display:flex;align-items:center;gap:8px}
.f-link::before{content:"";width:4px;height:4px;border-radius:50%;background:#fff}
.f-link.on{color:var(--orange)}
.f-link.on::before{background:var(--orange)}
.f-divider{position:absolute;left:342px;top:36px;width:1px;height:220px;background:#222}
.f-ico{position:absolute;left:412px;width:24px;height:24px;border-radius:3px;background:var(--blue);display:flex;align-items:center;justify-content:center}
.f-text{position:absolute;left:446px;font-size:11px;line-height:16px}
.f-text small{font-size:10px;color:#ccc;display:block}
.f-social{position:absolute;top:3532px;width:22px;height:22px;border-radius:50%;background:#fff}
.map{position:absolute;left:650px;top:3266px;width:550px;height:316px;background:linear-gradient(135deg,#eeeeee,#e2e2e2 50%,#f1f1f1)}
.map-notch{position:absolute;left:650px;top:3266px}
.copyright{position:absolute;left:0;top:3582px;width:1200px;height:35px;background:#fff;text-align:center;font-size:10.5px;line-height:35px;color:#111}
</style>
</head>
<body>

<section class="hero">
  <div class="hero-photo" role="img" aria-label="Hand placing a small wooden house among a row of wooden house models"></div>
  <h1 class="hero-title display">LANTERN INSURANCE<br>BROKERS</h1>
  <p class="hero-sub">We Are A New Insurance Brokerage Firm Dealing Exclusively With Companies.</p>
  <span class="btn-dot" style="left:144px;top:398px"></span>
  <a class="btn" style="left:166px;top:393px;width:116px">CONTACT US</a>
  <div class="mouse"><svg width="50" height="40" viewBox="0 0 50 40"><rect x="20" y="14" width="10" height="16" rx="5" fill="none" stroke="#f2612a" stroke-width="1.5"/><line x1="25" y1="18" x2="25" y2="22" stroke="#f2612a" stroke-width="1.5"/></svg></div>
</section>

<header class="site-header">
  <div class="brand"><span class="brand-dot"></span>Lantern-Brokers</div>
  <span class="nav active" style="left:324px">HOME</span>
  <span class="nav" style="left:392px">WHO WE ARE</span>
  <span class="nav" style="left:501px">WHAT WE DO</span>
  <span class="nav" style="left:612px">TESTIMONIAL</span>
  <span class="nav" style="left:727px">OUR TEAM</span>
  <span class="nav" style="left:821px">CONTACT US</span>
  <div class="phone"><span class="phone-ring"><svg width="12" height="12" viewBox="0 0 24 24"><path d="M6.6 10.8a15 15 0 0 0 6.6 6.6l2.2-2.2a1 1 0 0 1 1-.25 11.4 11.4 0 0 0 3.6.57 1 1 0 0 1 1 1V20a1 1 0 0 1-1 1A17 17 0 0 1 3 4a1 1 0 0 1 1-1h3.5a1 1 0 0 1 1 1c0 1.25.2 2.45.57 3.6a1 1 0 0 1-.25 1z" fill="#f2612a"/></svg></span>(555) 218 4400</div>
</header>

<!-- who we are -->
<p class="kicker" style="top:693px">About Us</p>
<h2 class="sec-title display" style="top:710px">Who We Are</h2>
<span class="sec-rule" style="top:754px"></span>
<p class="sec-lead" style="top:766px">Lorem ipsum dolor sit amet, consectetuer adipiscing elit, sed diam nonummy nibh euismod tincidunt ut laoreet dolore magna</p>
<div class="about-photo"><div role="img" aria-label="Broker handing a contract to a client across a desk"></div></div>
<h3 class="about-heading">WELCOME TO LANTERN INSURANCE<br>BROKERS</h3>
<p class="about-text">Lorem Ipsum Dolor Sit Amet, Consectetuer Adipiscing Elit, Sed Diam Nonummy Nibh Euismod Tincidunt Ut Laoreet Dolore Magna Aliquam Erat Volutpat. Ut Wisi Enim Ad Minim Veniam, Quis Nostrud Exerci Tation Ullamcorper Suscipit Lobortis Nisl Ut Aliquip Ex Ea Commodo Consequat. Duis Autem Vel Eum Iriure Dolor In Hendrerit In Vulputate Velit Esse Molestie Consequat, Vel Illum Dolore Eu Feugiat Nulla Facilisis At Vero Eros Et Accumsan Et Iusto Odio Dignissim Qui Blandit Praesent Luptatum Zzril Delenit Augue Duis Dolore Te Feugait Nulla Facilisi. Lorem Ipsum Dolor Sit Amet, Consectetuer Adipiscing Elit.</p>
<span class="about-stem"></span>
<span class="btn-dot" style="left:643px;top:1071px"></span>
<a class="btn" style="left:665px;top:1067px;width:113px">CONTACT US</a>

<!-- services -->
<section class="services"></section>
<p class="kicker" style="top:1241px">Services</p>
<h2 class="sec-title display" style="top:1256px">What We Do</h2>
<span class="sec-rule" style="top:1300px"></span>
<p class="sec-lead" style="top:1316px">Lorem ipsum dolor sit amet, consectetuer adipiscing elit, sed diam nonummy nibh euismod tincidunt ut laoreet dolore magna</p>

<div class="service" style="left:114px">
  <svg width="142" height="142" viewBox="0 0 142 142"><circle cx="71" cy="71" r="56" fill="#fff"/><path d="M71 4 A67 67 0 0 1 138 71" fill="none" stroke="#1b8fe6" stroke-width="5"/><path d="M71 138 A67 67 0 0 1 4 71" fill="none" stroke="#1b8fe6" stroke-width="5"/><path d="M28 38 A56 56 0 0 1 114 38" fill="none" stroke="#1b8fe6" stroke-width="3"/><path d="M71 52 l14 5 v10 c0 9-6 15-14 18 c-8-3-14-9-14-18 v-10z M71 58 v22 M60 67 h22" fill="none" stroke="#222" stroke-width="2"/><path d="M50 74 v14 l10 8 M92 74 v14 l-10 8" fill="none" stroke="#222" stroke-width="2"/></svg>
  <p class="service-label">Liabilities<br>Insurance</p>
</div>
<div class="service" style="left:309px">
  <svg width="142" height="142" viewBox="0 0 142 142"><circle cx="71" cy="71" r="56" fill="#fff"/><path d="M71 4 A67 67 0 0 1 138 71" fill="none" stroke="#1b8fe6" stroke-width="5"/><path d="M71 138 A67 67 0 0 1 4 71" fill="none" stroke="#1b8fe6" stroke-width="5"/><path d="M28 38 A56 56 0 0 1 114 38" fill="none" stroke="#1b8fe6" stroke-width="3"/><circle cx="71" cy="71" r="30" fill="none" stroke="#222" stroke-width="2"/><path d="M52 78 l5-10 h26 l5 10 v6 h-36z" fill="#222"/><circle cx="60" cy="86" r="3" fill="#fff"/><circle cx="82" cy="86" r="3" fill="#fff"/></svg>
  <p class="service-label">Automobile<br>Insurance</p>
</div>
<div class="service featured" style="left:504px">
  <svg width="142" height="142" viewBox="0 0 142 142"><circle cx="71" cy="71" r="56" fill="#fff"/><path d="M71 4 A67 67 0 0 1 138 71" fill="none" stroke="#f2612a" stroke-width="5"/><path d="M71 138 A67 67 0 0 1 4 71" fill="none" stroke="#f2612a" stroke-width="5"/><path d="M28 38 A56 56 0 0 1 114 38" fill="none" stroke="#f2612a" stroke-width="3"/><path d="M50 88 h42 M54 88 v-22 h34 v22 M60 66 v-10 h10 v10 M76 66 v-14 M58 74 h26 M58 80 h26" fill="none" stroke="#f2612a" stroke-width="2"/></svg>
  <p class="service-label">Construction And<br>Engineering</p>
</div>
<div class="service" style="left:698px">
  <svg width="142" height="142" viewBox="0 0 142 142"><circle cx="71" cy="71" r="56" fill="#fff"/><path d="M71 4 A67 67 0 0 1 138 71" fill="none" stroke="#1b8fe6" stroke-width="5"/><path d="M71 138 A67 67 0 0 1 4 71" fill="none" stroke="#1b8fe6" stroke-width="5"/><path d="M28 38 A56 56 0 0 1 114 38" fill="none" stroke="#1b8fe6" stroke-width="3"/><path d="M71 47 l20 7 v14 c0 12-9 20-20 24 c-11-4-20-12-20-24 v-14z" fill="none" stroke="#222" stroke-width="2.5"/><path d="M66 60 h10 v8 h8 v10 h-8 v8 h-10 v-8 h-8 v-10 h8z" fill="none" stroke="#222" stroke-width="2"/></svg>
  <p class="service-label">Casualty Workmen 's<br>Compensation Health Insurance</p>
</div>
<div class="service" style="left:893px">
  <svg width="142" height="142" viewBox="0 0 142 142"><circle cx="71" cy="71" r="56" fill="#fff"/><path d="M71 4 A67 67 0 0 1 138 71" fill="none" stroke="#1b8fe6" stroke-width="5"/><path d="M71 138 A67 67 0 0 1 4 71" fill="none" stroke="#1b8fe6" stroke-width="5"/><path d="M28 38 A56 56 0 0 1 114 38" fill="none" stroke="#1b8fe6" stroke-width="3"/><rect x="47" y="54" width="48" height="24" fill="none" stroke="#222" stroke-width="2"/><circle cx="71" cy="66" r="7" fill="none" stroke="#222" stroke-width="2"/><circle cx="60" cy="86" r="5" fill="#222"/><circle cx="82" cy="86" r="5" fill="#222"/></svg>
  <p class="service-label">Marime And Transit<br>Credit</p>
</div>

<!-- testimonial -->
<section class="testimonial" role="img" aria-label="Businessman's hand on a row of wooden blocks, darkened background"></section>
<div class="t-layer" style="top:1628px">
  <p class="kicker" style="top:66px;color:#fff">Testimonial</p>
  <h2 class="sec-title display" style="top:82px;color:#fff">What Our Clients Say</h2>
  <span class="sec-rule" style="top:126px"></span>
  <p class="sec-lead" style="top:133px;color:#fff">Lorem ipsum dolor sit amet, consectetuer adipiscing elit, sed diam nonummy nibh euismod tincidunt ut laoreet dolore magna</p>
  <div class="avatar" role="img" aria-label="Client portrait"></div>
  <p class="t-name">Clients Name</p>
  <p class="t-role">- Designer</p>
  <p class="t-quote">Lorem ipsum dolor sit amet, consectetuer adipiscing elit, sed diam nonummy nibh euismod tincidunt ut laoreet dolore magna aliquam erat volutpat. Ut wisi enim ad minim veniam, quis nostrud exerci tation ullamcorper suscipit lobortis nisl ut aliquip ex ea commodo consequat. Duis autem vel eum iriure dolor in hendrerit in vulputate velit esse molestie consequat, vel illum dolore eu feugiat nulla facilisis at vero eros et accumsan et iusto odio dignissim qui blandit praesent luptatum zzril delenit augue duis dolore te feugait nulla facilisi.</p>
  <div class="dots"><span></span><span class="on"></span><span></span></div>
</div>

<!-- team -->
<p class="kicker" style="top:2133px">Our Team</p>
<h2 class="sec-title display" style="top:2147px">Lantern Insurance Team</h2>
<span class="sec-rule" style="top:2192px"></span>
<p class="sec-lead" style="top:2207px">Lorem ipsum dolor sit amet, consectetuer adipiscing elit, sed diam nonummy nibh euismod tincidunt ut laoreet dolore magna</p>

<article class="member" style="left:143px"><div class="member-photo" role="img" aria-label="Team member portrait in dark suit"></div><p class="member-name">Your Name</p><p class="member-role">General Manager</p><p class="member-bio">Lorem ipsum dolor sit amet, rtetuer adipiscinger elit werr werr veniam werwerr erenwer.</p></article>
<article class="member" style="left:378px"><div class="member-photo" role="img" aria-label="Team member portrait in dark suit"></div><div class="member-social"><span></span><span></span><span></span></div><p class="member-name">Your Name</p><p class="member-role">General Manager</p><p class="member-bio">Lorem ipsum dolor sit amet, rtetuer adipiscinger elit werr werr veniam werwerr erenwer.</p></article>
<article class="member" style="left:612px"><div class="member-photo" role="img" aria-label="Team member portrait in dark suit"></div><p class="member-name">Your Name</p><p class="member-role">General Manager</p><p class="member-bio">Lorem ipsum dolor sit amet, rtetuer adipiscinger elit werr werr veniam werwerr erenwer.</p></article>
<article class="member" style="left:846px"><div class="member-photo" role="img" aria-label="Team member portrait in dark suit"></div><p class="member-name">Your Name</p><p class="member-role">General Manager</p><p class="member-bio">Lorem ipsum dolor sit amet, rtetuer adipiscinger elit werr werr veniam werwerr erenwer.</p></article>

<!-- contact -->
<section class="contact"></section>
<p class="kicker" style="top:2686px">Get in Touch</p>
<h2 class="sec-title display" style="top:2705px">Contact Us</h2>
<span class="sec-rule" style="top:2754px"></span>
<p class="sec-lead" style="top:2770px">Lorem ipsum dolor sit amet, consectetuer adipiscing elit, sed diam nonummy nibh euismod tincidunt ut laoreet dolore magna</p>
<div class="field" style="left:143px;top:2810px;width:449px">First Name*</div>
<div class="field" style="left:610px;top:2810px;width:449px">Last Name*</div>
<div class="field" style="left:143px;top:2863px;width:449px">Email*</div>
<div class="field" style="left:610px;top:2863px;width:449px">Company Name*</div>
<div class="field" style="left:143px;top:2916px;width:449px">Your Tittle*</div>
<div class="field" style="left:610px;top:2916px;width:449px">Phone*</div>
<div class="field message" style="left:143px;top:2970px;width:913px">Message*</div>
<span class="btn-dot" style="left:534px;top:3097px"></span>
<a class="btn" style="left:556px;top:3093px;width:115px">SUBMIT</a>

<!-- newsletter -->
<section class="newsletter">
  <span class="nl-icon"><svg width="16" height="12" viewBox="0 0 16 12"><rect x="1" y="1" width="14" height="10" fill="none" stroke="#fff" stroke-width="1.5"/><path d="M1 1 l7 6 l7-6" fill="none" stroke="#fff" stroke-width="1.5"/></svg></span>
  <h3 class="nl-title display">Newsletter Signup</h3>
  <svg class="abs" style="left:438px;top:16px" width="24" height="40" viewBox="0 0 24 40"><path d="M3 2 L20 20 L3 38" fill="none" stroke="#fff" stroke-width="1.5"/></svg>
  <div class="nl-input">Your e-mail</div>
  <div class="nl-btn">SIGN UP</div>
</section>

<!-- footer -->
<footer class="footer">
  <h4 class="f-head display" style="left:143px">QUICK LINK</h4>
  <span class="f-rule" style="left:143px"></span>
  <span class="f-link on" style="top:83px">HOME</span>
  <span class="f-link" style="top:112px">WHO WE ARE</span>
  <span class="f-link" style="top:142px">WHAT WE DO</span>
  <span class="f-link" style="top:167px">TESTIMONIAL</span>
  <span class="f-link" style="top:194px">OUR TEAM</span>
  <span class="f-link" style="top:225px">CONTACT US</span>
  <span class="f-divider"></span>

  <h4 class="f-head display" style="left:414px">GET IN TOUCH</h4>
  <span class="f-rule" style="left:414px"></span>
  <span class="f-ico" style="top:86px"><svg width="10" height="14" viewBox="0 0 10 14"><path d="M5 0a5 5 0 0 1 5 5c0 4-5 9-5 9S0 9 0 5a5 5 0 0 1 5-5z" fill="#fff"/><circle cx="5" cy="5" r="2" fill="#1b8fe6"/></svg></span>
  <p class="f-text" style="top:84px;font-size:14px">Lantern Insurance<small>Lorem Ipsum Dolor Sit Amet,<br>Adipiscinger Elit Werr.</small></p>
  <span class="f-ico" style="top:157px"><svg width="12" height="12" viewBox="0 0 24 24"><path d="M6.6 10.8a15 15 0 0 0 6.6 6.6l2.2-2.2a1 1 0 0 1 1-.25 11.4 11.4 0 0 0 3.6.57 1 1 0 0 1 1 1V20a1 1 0 0 1-1 1A17 17 0 0 1 3 4a1 1 0 0 1 1-1h3.5a1 1 0 0 1 1 1c0 1.25.2 2.45.57 3.6a1 1 0 0 1-.25 1z" fill="#fff"/></svg></span>
  <p class="f-text" style="top:162px">+555 218 4400</p>
  <span class="f-ico" style="top:214px"><svg width="12" height="9" viewBox="0 0 16 12"><rect x="1" y="1" width="14" height="10" fill="none" stroke="#fff" stroke-width="1.6"/><path d="M1 1 l7 6 l7-6" fill="none" stroke="#fff" stroke-width="1.6"/></svg></span>
  <p class="f-text" style="top:219px">info@lanternbrokers-mail.com</p>
</footer>
<span class="f-social" style="left:412px"></span>
<span class="f-social" style="left:440px"></span>
<span class="f-social" style="left:469px"></span>

<div class="map" role="img" aria-label="Street map showing the office location with a red pin"></div>
<svg class="map-notch" width="30" height="316" viewBox="0 0 30 316"><path d="M0 0 L0 316 L0 316 L0 190 L26 158 L0 126 Z" fill="#0b0b0b"/></svg>
<svg class="abs" style="left:992px;top:3358px" width="20" height="28" viewBox="0 0 20 28"><path d="M10 0a10 10 0 0 1 10 10c0 8-10 18-10 18S0 18 0 10A10 10 0 0 1 10 0z" fill="#e32222"/><circle cx="10" cy="10" r="4" fill="#fff"/></svg>

<div class="copyright">Copyright 2019 Lantern Insurance Brokers. All Rights Reserved.</div>

</body>
</html>
```